New Website Design for PHOVAN.org

We are looking for a new website design for PHOVAN.org. PHOVAN is a non profit home inspector association based in California. Home Inspectors are people that come out and look at a house before it's purchased to let the buyer know of any defects that may exist.
Our site is based on Joomla so if you'll be able to make a Joomla 3 template as well, please let us know (not required, but a bonus).
We would like to see designs that incorporate royal blue, white and chrome into the site as that's our main business colors.
We would like a place for rotating banners though they don't need to be the same size as the current site.
We would like navigation to be easier to manage with menus only across the top (via drop down menus) where we are going to sort out the items currently on the side. Possibly the front page could have a graphic link to separate portals for Realtors, Home Buyers and Inspectors, but that's just one option.
We would like a good mobile design or something that will scale easily to mobile.
The Find an Inspector feature is important and should stand out. The ASK PHOVANr site
Current home page feels a bit busy. Would like to simplify a bit.

```html
<!DOCTYPE html>
<html lang="en">
<head>
<meta charset="utf-8">
<title>PHOVAN – Home Inspection Association</title>
<link href="https://fonts.googleapis.com/css2?family=Ubuntu:wght@400;500&family=Open+Sans:wght@300;400;600&family=PT+Sans:wght@400;700&display=swap" rel="stylesheet">
<style>
:root{
  --royal:#3b4c9b;
  --royal-dark:#26357a;
  --brand-text:#4a5fab;
  --ink:#2a2a2a;
  --muted:#8a8a8a;
  --heading:#555;
  --hero-bg:#dfe5dc;
  --footer:#2b2b2b;
}
*{margin:0;padding:0;box-sizing:border-box}
html,body{width:1189px;height:1200px;overflow:hidden;background:#fff}
body{position:relative;font-family:"Ubuntu",sans-serif;color:var(--ink)}
.abs{position:absolute}

/* header */
.brand{left:119px;top:13px;display:flex;align-items:center;gap:18px}
.brand-mark{width:70px;height:70px;border-radius:50%;background:#e9eaef;border:2px solid #b7bac6}
.brand-name{font-weight:500;font-size:17px;line-height:22px;color:var(--brand-text);text-transform:uppercase}
.contact{right:122px;top:9px;font-family:"Open Sans",sans-serif;font-size:18px;line-height:26px;display:grid;grid-template-columns:62px auto;white-space:nowrap}
.contact dt{color:var(--brand-text)}
.contact dd{color:#222;text-align:right}

/* hero */
.hero-bg{left:0;top:92px;width:1189px;height:517px;background:var(--hero-bg)}
.hero-photo{left:470px;top:92px;width:719px;height:552px;
  background:linear-gradient(90deg,#dfe5dc 0%,#d5dcd2 35%,#bfc8b8 60%,#8d9a78 80%,#55663d 100%)}
.nav{left:119px;top:92px;width:951px;height:55px;background:#fff;box-shadow:0 6px 8px -4px rgba(0,0,0,.35);display:flex;align-items:center;padding-left:18px}
.nav a{font-family:"Open Sans",sans-serif;font-size:15px;color:#8a8a8a;text-decoration:none;margin-right:33px}
.nav a.current{color:var(--royal)}
.social{position:absolute;right:8px;top:16px;display:flex;gap:7px}
.social span{width:25px;height:23px;border:1px solid #bbb;background:linear-gradient(#fafafa,#ddd);border-radius:2px}

.hero-copy{left:119px;top:243px;width:395px}
.hero-copy .kicker{font-family:"PT Sans",sans-serif;font-size:28px;color:var(--royal);line-height:32px}
.hero-copy h1{font-family:"PT Sans",sans-serif;font-weight:700;font-size:32px;color:var(--royal);line-height:36px;margin-bottom:12px}
.hero-copy p{font-size:12.5px;line-height:19px;color:#111;letter-spacing:-.2px}
.btn{display:inline-block;background:linear-gradient(#4d5fb0,var(--royal-dark));color:#fff;border:1px solid #1d2a66;border-radius:3px;font-weight:500}
.hero-copy .btn{margin-top:16px;font-size:15px;padding:8px 12px}
.dots{left:578px;top:495px;display:flex;gap:4px;align-items:center}
.dots i{width:7px;height:7px;border-radius:50%;background:#b9bec0}
.dots i.on{width:10px;height:10px;background:var(--royal)}

/* band */
.band{left:109px;top:524px;width:982px;height:185px;background:linear-gradient(#e4e4e8,#fff)}
.band p{position:absolute;left:24px;top:19px;width:740px;font-family:"Open Sans",sans-serif;font-weight:300;font-size:28px;line-height:36px;color:#555}
.find-btn{position:absolute;left:777px;top:26px;width:178px;height:59px;border-radius:30px;background:linear-gradient(#5567b8,var(--royal-dark));color:#fff;font-family:"Open Sans",sans-serif;font-weight:600;font-size:15px;display:flex;align-items:center;justify-content:center;box-shadow:0 4px 6px rgba(0,0,0,.3)}

/* portals */
.portals{left:130px;top:653px;display:flex;gap:20px}
.portal{width:220px}
.portal svg{display:block}
.portal h2{font-family:"Open Sans",sans-serif;font-weight:600;font-size:20px;color:var(--heading);margin:8px 0 14px 2px}
.portal p{font-size:12px;line-height:18px;color:var(--muted);letter-spacing:.4px}
.more{display:block;margin-top:12px;font-size:12px;color:var(--royal-dark);letter-spacing:.3px}
.more::before{content:"›";font-weight:700;margin-right:6px}

/* welcome & login */
.section-title{font-family:"Open Sans",sans-serif;font-weight:600;font-size:20px;color:var(--heading);display:flex;align-items:center;gap:8px;white-space:nowrap}
.section-title::after{content:"";flex:1;border-top:2px dotted #ccc}
.section-title b{font-weight:600;color:var(--royal)}
.welcome{left:127px;top:937px;width:662px}
.welcome p{font-size:12px;line-height:18px;color:var(--muted);letter-spacing:.4px;width:645px;margin-top:6px;margin-bottom:18px}
.welcome .btn{font-size:13px;padding:6px 8px;margin-top:-2px}
.login{left:835px;top:937px;width:231px}
.login label{display:block;font-size:12px;color:#777;letter-spacing:.3px;margin:16px 0 4px 3px}
.login label+span{display:block;margin-left:3px;height:26px;border:1px solid #ddd;background:linear-gradient(#f4f4f4,#fff)}
.login label:nth-of-type(2){margin-top:10px}
.login .row{display:flex;justify-content:space-between;align-items:center;margin-top:30px;padding-right:8px}
.login .btn{font-size:13px;padding:5px 18px;border-radius:2px}
.login a{font-size:11px;color:var(--royal-dark);text-decoration:underline}

/* footer */
.footer{left:0;top:1156px;width:1189px;height:44px;background:var(--footer);color:#ccc;font-size:11px;display:flex;justify-content:space-between;align-items:center;padding:0 118px 0 126px}
</style>
</head>
<body>
<header>
  <div class="abs brand"><span class="brand-mark"></span><span class="brand-name">Pacific Home Inspection<br>Network Association</span></div>
  <dl class="abs contact"><dt>Phone:</dt><dd>(800) 555-0142</dd><dt>Fax:</dt><dd>(916) 555-0187</dd></dl>
</header>

<div class="abs hero-bg"></div>
<div class="abs hero-photo" role="img" aria-label="Photo of a home inspector checking exterior siding of a house"></div>

<nav class="abs nav">
  <a class="current">Home</a><a>Find an Inspector</a><a>Home Buyers &amp; Sellers</a><a>Real Estate Agents</a><a>Inspectors</a><a>Ask Phovan</a>
  <div class="social"><span></span><span></span><span></span><span></span></div>
</nav>

<section class="abs hero-copy">
  <div class="kicker">The Leader in</div>
  <h1>Home Inspection Service</h1>
  <p>Le Lorem Ipsum est simplement du faux texte employé dans la composition et la mise en page avant impression. Le Lorem Ipsum est le faux.</p>
  <span class="btn">Read More</span>
</section>
<div class="abs dots"><i></i><i></i><i class="on"></i><i></i></div>

<section class="abs band">
  <p>Le Lorem Ipsum est simplement du faux texte employé dans la composition et la mise en page avant impression.</p>
  <span class="find-btn">FIND INSPECTOR</span>
</section>

<section class="abs portals">
  <article class="portal">
    <svg width="56" height="56" viewBox="0 0 56 56"><circle cx="28" cy="28" r="27" fill="var(--royal)"/><path d="M14 28 28 16 42 28M18 26v14h20V26" fill="none" stroke="#fff" stroke-width="2.5"/><rect x="22" y="30" width="12" height="7" fill="none" stroke="#fff" stroke-width="1.5"/></svg>
    <h2>Home Realtors</h2>
    <p>Lorem ipsum dolor sit amet, consecte-tur adipisicing elit, sed do eiusmod tempor incididunt ut labore et dolore magna aliqua. Ut enim ad minim veniam, quis nostrud exercitation ullamco laboris nisi ut aliquip ex ea commodo consequat.</p>
    <span class="more">Read more</span>
  </article>
  <article class="portal">
    <svg width="56" height="56" viewBox="0 0 56 56"><circle cx="28" cy="28" r="27" fill="var(--royal)"/><path d="M14 28 28 16 42 28M18 26v14h20V26" fill="none" stroke="#fff" stroke-width="2.5"/><circle cx="25" cy="34" r="3" fill="none" stroke="#fff" stroke-width="2"/><path d="M28 34h12" stroke="#fff" stroke-width="2"/></svg>
    <h2>Home Buyers</h2>
    <p>Lorem ipsum dolor sit amet, consecte-tur adipisicing elit, sed do eiusmod tempor incididunt ut labore et dolore magna aliqua. Ut enim ad minim veniam, quis nostrud exercitation ullamco laboris nisi ut aliquip ex ea commodo consequat.</p>
    <span class="more">Read more</span>
  </article>
  <article class="portal">
    <svg width="56" height="56" viewBox="0 0 56 56"><circle cx="28" cy="28" r="27" fill="var(--royal)"/><path d="M14 28 28 16 42 28M18 26v14h20V26" fill="none" stroke="#fff" stroke-width="2.5"/><circle cx="28" cy="32" r="4" fill="none" stroke="#fff" stroke-width="2"/><path d="M31 35l6 5" stroke="#fff" stroke-width="2.5"/></svg>
    <h2>Home Inspectors</h2>
    <p>Lorem ipsum dolor sit amet, consecte-tur adipisicing elit, sed do eiusmod tempor incididunt ut labore et dolore magna aliqua. Ut enim ad minim veniam, quis nostrud exercitation ullamco laboris nisi ut aliquip ex ea commodo consequat.</p>
    <span class="more">Read more</span>
  </article>
  <article class="portal">
    <svg width="56" height="56" viewBox="0 0 56 56"><circle cx="28" cy="28" r="27" fill="var(--royal)"/><path d="M17 17l22 22M39 17 17 39" stroke="#fff" stroke-width="4" stroke-linecap="round"/></svg>
    <h2>Other Services</h2>
    <p>Lorem ipsum dolor sit amet, consecte-tur adipisicing elit, sed do eiusmod tempor incididunt ut labore et dolore magna aliqua. Ut enim ad minim veniam, quis nostrud exercitation ullamco laboris nisi ut aliquip ex ea commodo consequat.</p>
    <span class="more">Read more</span>
  </article>
</section>

<section class="abs welcome">
  <h2 class="section-title">Welcome To <b>PHOVAN</b></h2>
  <p>Lorem ipsum dolor sit amet, consectetur adipisicing elit, sed do eiusmod tempor incididunt ut labore et dolore magna aliqua. Ut enim ad minim veniam, quis nostrud exercitation ullamco laboris nisi ut aliquip ex ea com-modo consequat.</p>
  <p>Duis aute irure dolor in reprehenderit in voluptate velit esse cillum dolore eu fugiat nulla pariatur. Excepteur sint occaecat cupidatat non proident, sunt in culpa qui officia deserunt mollit anim id est laborum quis nostrud exer-citation ullamco laboris nisi ut aliquip ex ea commodo consequat.</p>
  <span class="btn">READ MORE</span>
</section>

<section class="abs login">
  <h2 class="section-title">Inspector Login</h2>
  <label>User name</label><span></span>
  <label>Password</label><span></span>
  <div class="row"><span class="btn">Login</span><a>Forgot Login?</a></div>
</section>

<footer class="abs footer">
  <span>Copyright © 2013 &nbsp;All Rights Reserved</span>
  <span>Terms &amp; Condition &nbsp;| &nbsp;Privacy Policy</span>
</footer>
</body>
</html>
```